Sparrow Haulage needs a business card design.

Design a double-sided business card for new freight business. On the front, would like to see our logo along with the following info:

Martin Obuya
CEO/FOUNDER
555-206-7142
martinobuya@sparrow-haulage.example

On the reverse side, we would like to use the graphic image of our logo only without the Sparrow Haulage name.

```html
<!DOCTYPE html>
<html lang="en">
<head>
<meta charset="utf-8">
<title>Sparrow Haulage — Business Card</title>
<link href="https://fonts.googleapis.com/css2?family=Archivo:wght@400;700;800&display=swap" rel="stylesheet">
<style>
  :root {
    --navy: #03035a;
    --red: #b30808;
    --white: #ffffff;
    --ink: #1c1c1c;
    --stage: #1f1f1f;
    --rule: #c9c9c9;
  }
  * { box-sizing: border-box; margin: 0; padding: 0; }
  html, body {
    width: 1200px; height: 1015px; overflow: hidden;
    background: var(--stage);
    font-family: "Archivo", Arial, sans-serif;
  }
  .card {
    position: absolute;
    width: 700px; height: 400px;
    overflow: hidden;
    box-shadow: 0 18px 40px rgba(0,0,0,.55);
  }

  /* Reverse side: mark only, no company name */
  .card--back { left: 150px; top: 70px; background: var(--navy); }
  .back-mark {
    position: absolute; left: 50%; top: 120px;
    width: 96px; height: 96px; margin-left: -48px;
    background: var(--red);
  }
  .back-url {
    position: absolute; left: 0; right: 0; bottom: 90px;
    text-align: center; font-size: 20px; letter-spacing: 1px;
    color: var(--white); text-transform: uppercase;
  }
  .back-url__domain { color: var(--red); }

  /* Front side */
  .card--front { left: 350px; top: 540px; background: var(--white); }
  .brand {
    position: absolute; left: 52px; top: 158px;
    display: flex; align-items: center; gap: 12px;
  }
  .brand__square { width: 30px; height: 30px; background: var(--red); flex: none; }
  .brand__name {
    color: var(--navy); font-weight: 800; font-size: 24px;
    letter-spacing: 3px; text-transform: uppercase; line-height: 1.05;
  }
  .brand__name span { display: block; }
  .divider {
    position: absolute; left: 318px; top: 40px; width: 1px; height: 240px;
    background: linear-gradient(to bottom, transparent, var(--rule) 30%, var(--rule) 70%, transparent);
  }
  .contact { position: absolute; left: 346px; top: 74px; }
  .contact__name {
    font-weight: 800; font-size: 30px; letter-spacing: .5px;
    text-transform: uppercase; color: var(--navy); line-height: 1;
  }
  .contact__surname { color: var(--red); }
  .contact__title {
    margin-top: 6px; font-size: 18px; color: var(--ink);
    text-transform: uppercase; letter-spacing: .5px;
  }
  .contact__list { list-style: none; margin-top: 26px; }
  .contact__item {
    display: flex; align-items: center; gap: 10px;
    font-size: 15.5px; color: var(--ink); line-height: 1; margin-bottom: 9px;
  }
  .contact__icon { width: 16px; height: 16px; flex: none; fill: var(--red); }
  .contact__domain { color: var(--navy); }
  .contact__domain b { color: var(--red); font-weight: 400; }

  .band { position: absolute; bottom: 0; }
  .band--navy { left: 0; width: 430px; height: 14px; background: var(--navy); }
  .band--red { left: 438px; right: 0; height: 36px; background: var(--red); }
</style>
</head>
<body>

<section class="card card--back" aria-label="Card reverse">
  <div class="back-mark" role="img" aria-label="Sparrow Haulage mark"></div>
  <p class="back-url">www.<span class="back-url__domain">sparrow-haulage</span>.example</p>
</section>

<section class="card card--front" aria-label="Card front">
  <div class="brand">
    <span class="brand__square"></span>
    <span class="brand__name"><span>Sparrow</span><span>Haulage</span></span>
  </div>

  <div class="divider"></div>

  <div class="contact">
    <h1 class="contact__name">Martin <span class="contact__surname">Obuya</span></h1>
    <p class="contact__title">CEO/Founder</p>
    <ul class="contact__list">
      <li class="contact__item">
        <svg class="contact__icon" viewBox="0 0 24 24"><path d="M6.6 10.8a15.1 15.1 0 0 0 6.6 6.6l2.2-2.2a1 1 0 0 1 1-.25 11.4 11.4 0 0 0 3.6.57 1 1 0 0 1 1 1V20a1 1 0 0 1-1 1A17 17 0 0 1 3 4a1 1 0 0 1 1-1h3.5a1 1 0 0 1 1 1c0 1.25.2 2.45.57 3.57a1 1 0 0 1-.25 1z"/></svg>
        555-206-7142
      </li>
      <li class="contact__item">
        <svg class="contact__icon" viewBox="0 0 24 24"><path d="M2 5h20v14H2z"/><path d="M2 5l10 8 10-8" fill="none" stroke="#fff" stroke-width="1.8"/></svg>
        martinobuya@sparrow-haulage.example
      </li>
      <li class="contact__item">
        <svg class="contact__icon" viewBox="0 0 24 24"><circle cx="12" cy="12" r="10"/><path d="M2 12h20M12 2c3 3 3 17 0 20M12 2c-3 3-3 17 0 20M4 7h16M4 17h16" fill="none" stroke="#fff" stroke-width="1.3"/></svg>
        <span>www.<span class="contact__domain">sparrow-<b>haulage</b></span>.example</span>
      </li>
    </ul>
  </div>

  <div class="band band--navy"></div>
  <div class="band band--red"></div>
</section>

</body>
</html>
```